Design a building access mobile app for Quillo by Tamberlin Entry Systems

Hello, We're looking for an awesome designer to create an app design for our app Quillo, by Tamberlin Entry Systems. the mobile app allows employees open their office doors with their mobile phone. this means they don't have to use those plastic card badges or keys. We like clean modern design, dark and light themes. We don't have a logo yet.
Updates

Reason: Waiting on a couple designers to submit concepts

Target Market(s)

Commercial and employees

Industry/Entity Type

Building

Font styles to use
Sans Serif
Other font styles liked:
• Oswald extra light

Requirements
Must have
• nice clean design

```html
<!DOCTYPE html>
<html lang="en">
<head>
<meta charset="utf-8">
<title>Quillo – Sign In</title>
<link rel="stylesheet" href="https://fonts.googleapis.com/css2?family=Oswald:wght@200;300;400&family=Roboto:wght@400;500&display=swap">
<style>
  :root {
    --stage: #1c9bd4;
    --screen: #ffffff;
    --ink: #111111;
    --muted: #9a9a9a;
    --rule: #e4e4e4;
    --accent: #3a7fc8;
    --brand: #23538d;
  }
  * { box-sizing: border-box; margin: 0; padding: 0; }
  html, body { width: 1200px; height: 864px; overflow: hidden; }
  body {
    background: var(--stage);
    font-family: "Oswald", "Roboto", sans-serif;
    position: relative;
  }
  .screen {
    position: absolute;
    left: 390px; top: 59px;
    width: 420px; height: 746px;
    background: var(--screen);
    box-shadow: 0 20px 50px rgba(0, 40, 80, 0.35);
  }
  .status-bar {
    position: absolute; left: 0; right: 0; top: 0; height: 24px;
    display: flex; align-items: center; justify-content: space-between;
    padding: 0 8px;
    font-family: "Roboto", sans-serif; font-size: 12px; color: var(--ink);
  }
  .status-left, .status-right { display: flex; align-items: center; gap: 5px; width: 120px; }
  .status-right { justify-content: flex-end; }
  .status-time { font-weight: 500; }
  .signal { letter-spacing: -1px; font-size: 9px; }
  .brand {
    position: absolute; left: 0; right: 0; top: 120px;
    display: flex; align-items: center; justify-content: center; gap: 12px;
  }
  .brand-dot { width: 22px; height: 22px; border-radius: 50%; background: var(--brand); }
  .brand-name { font-size: 44px; font-weight: 300; color: var(--brand); letter-spacing: 1px; }
  .field {
    position: absolute; left: 40px; right: 40px; height: 40px;
    display: flex; align-items: flex-end; gap: 20px;
  }
  .field-email { top: 290px; }
  .field-password { top: 350px; }
  .field svg { flex: none; margin-bottom: 8px; }
  .field-input {
    flex: 1; height: 100%;
    border-bottom: 1px solid var(--rule);
    display: flex; align-items: flex-end; padding-bottom: 8px;
    font-size: 16px; font-weight: 200; color: var(--muted);
  }
  .login-button {
    position: absolute; left: 48px; right: 48px; top: 440px; height: 50px;
    border-radius: 25px; background: var(--accent); border: 0;
    color: #ffffff; font-family: "Oswald", sans-serif; font-weight: 300;
    font-size: 17px; letter-spacing: 1px;
  }
  .forgot {
    position: absolute; left: 0; right: 0; top: 512px; text-align: center;
    font-size: 16px; font-weight: 300; color: var(--ink);
  }
  .divider {
    position: absolute; left: 40px; right: 40px; top: 562px;
    display: flex; align-items: center; gap: 14px;
    font-size: 11px; font-weight: 300; color: var(--muted);
  }
  .divider::before, .divider::after { content: ""; flex: 1; height: 1px; background: var(--rule); }
  .signup {
    position: absolute; left: 0; right: 0; top: 604px; text-align: center;
    font-size: 16px; font-weight: 200; color: var(--muted);
  }
  .signup-link { color: var(--accent); font-weight: 300; }
</style>
</head>
<body>
  <main class="screen">
    <div class="status-bar">
      <div class="status-left">
        <span class="signal">●●●○○</span>
        <span class="carrier">Nimbo</span>
        <svg width="13" height="10" viewBox="0 0 13 10" aria-hidden="true">
          <path d="M1 3.5a8 8 0 0 1 11 0M3 5.7a5 5 0 0 1 7 0M5 7.8a2 2 0 0 1 3 0" fill="none" stroke="#111" stroke-width="1.4" stroke-linecap="round"/>
        </svg>
      </div>
      <div class="status-time">1:23 AM</div>
      <div class="status-right">
        <svg width="7" height="11" viewBox="0 0 7 11" aria-hidden="true">
          <path d="M1 3l5 5-2.5 2V1L6 3 1 8" fill="none" stroke="#111" stroke-width="1"/>
        </svg>
        <span>77%</span>
        <svg width="24" height="11" viewBox="0 0 24 11" aria-hidden="true">
          <rect x="0.5" y="0.5" width="20" height="10" rx="2" fill="none" stroke="#111"/>
          <rect x="2" y="2" width="13.5" height="7" rx="1" fill="#111"/>
          <rect x="21.5" y="3.5" width="1.5" height="4" fill="#111"/>
        </svg>
      </div>
    </div>

    <div class="brand">
      <span class="brand-dot"></span>
      <span class="brand-name">Quillo</span>
    </div>

    <div class="field field-email">
      <svg width="22" height="16" viewBox="0 0 22 16" aria-hidden="true">
        <rect x="0.75" y="0.75" width="20.5" height="14.5" fill="none" stroke="#8a8a8a" stroke-width="1.2"/>
        <path d="M1 1l10 8 10-8M1 15l7-6M21 15l-7-6" fill="none" stroke="#8a8a8a" stroke-width="1.2"/>
      </svg>
      <div class="field-input">Email</div>
    </div>

    <div class="field field-password">
      <svg width="22" height="20" viewBox="0 0 22 20" aria-hidden="true">
        <path d="M6 9V6a5 5 0 0 1 10 0v3" fill="none" stroke="#8a8a8a" stroke-width="1.2"/>
        <rect x="3" y="9" width="16" height="10" rx="1" fill="none" stroke="#8a8a8a" stroke-width="1.2"/>
        <path d="M11 12.5v3" stroke="#8a8a8a" stroke-width="1.4" stroke-linecap="round"/>
      </svg>
      <div class="field-input">Password</div>
    </div>

    <button class="login-button" type="button">LOG IN</button>

    <p class="forgot">Forgot Password ?</p>

    <div class="divider">OR</div>

    <p class="signup">Don't have an Account ? <span class="signup-link">Sign Up</span></p>
  </main>
</body>
</html>
```